Local Roofing/Construction company business needs new biz card design

We need a new business card design, current cards are from the start of this operation and generic at best. We are a local Construction Company (General Contractor) with a majority of our work originating from insurance claims-exterior finish work is the main focus (Roofs-Siding-Gutters etc). Heavily involved with homeowners and the low ball offers they receive from insurance company's after a insurable event takes place. I have attached some of our original logo file(s) below.

```html
<!DOCTYPE html>
<html lang="en">
<head>
<meta charset="utf-8">
<title>Stonegate Builders – Business Card</title>
<link rel="stylesheet" href="https://fonts.googleapis.com/css2?family=Montserrat:wght@300;400;500;700;800&display=swap">
<style>
  :root {
    --page-bg: #1c1f21;
    --card-bg: #0f1c20;
    --card-back-bg: #14282d;
    --pattern-tone: #1b3237;
    --brand-green: #52b86a;
    --text-light: #f2f4f3;
  }
  * { box-sizing: border-box; margin: 0; padding: 0; }
  html, body {
    width: 1200px; height: 900px; overflow: hidden;
    background: var(--page-bg);
    font-family: "Montserrat", Arial, sans-serif;
  }
  .canvas {
    width: 1200px; height: 900px;
    display: flex; flex-direction: column; align-items: center; justify-content: center;
    gap: 48px;
  }
  .card {
    position: relative;
    width: 660px; height: 378px;
    border-radius: 24px;
    overflow: hidden;
    box-shadow: 0 14px 34px rgba(0,0,0,0.45);
  }
  /* Front */
  .card-front { background: var(--card-bg); }
  .bottom-band {
    position: absolute; left: 0; right: 0; bottom: 0; height: 15px;
    background: var(--brand-green);
  }
  .name-marker {
    position: absolute; left: 34px; top: 86px; width: 14px; height: 40px;
    background: var(--brand-green);
  }
  .person-name {
    position: absolute; left: 62px; top: 84px;
    font-size: 30px; font-weight: 700; letter-spacing: 2px;
    color: var(--brand-green); text-transform: uppercase;
  }
  .person-title {
    position: absolute; left: 62px; top: 124px;
    font-size: 17px; font-weight: 400; color: var(--text-light); letter-spacing: 0.5px;
  }
  .divider-line {
    position: absolute; left: 250px; right: 40px; top: 137px; height: 1.5px;
    background: var(--brand-green);
  }
  .contact-list {
    position: absolute; left: 34px; top: 166px;
    list-style: none; display: flex; flex-direction: column; gap: 9px;
  }
  .contact-item {
    display: flex; align-items: center; gap: 10px;
    font-size: 17px; font-weight: 400; color: var(--text-light); letter-spacing: 0.4px;
  }
  .contact-icon { width: 16px; height: 16px; flex: none; }
  .brand-lockup {
    position: absolute; right: 48px; top: 52px;
    display: flex; align-items: center; gap: 12px;
  }
  .brand-square { width: 22px; height: 22px; background: var(--brand-green); }
  .brand-name {
    font-size: 26px; font-weight: 800; letter-spacing: 1px;
    color: var(--brand-green); text-transform: uppercase;
  }
  .office-address {
    position: absolute; right: 44px; bottom: 48px; text-align: right;
    font-size: 17px; font-weight: 400; line-height: 1.5;
    color: var(--text-light); letter-spacing: 0.5px;
  }
  /* Back */
  .card-back { background: var(--card-back-bg); }
  .back-pattern-area {
    position: absolute; inset: 0;
    background: radial-gradient(ellipse at 60% 40%, var(--pattern-tone), var(--card-back-bg));
  }
  .back-brand {
    position: absolute; right: 40px; bottom: 34px;
    display: flex; align-items: center; gap: 10px;
  }
  .back-brand .brand-square { width: 16px; height: 16px; }
  .back-brand .brand-name { font-size: 17px; }
</style>
</head>
<body>
<main class="canvas">
  <section class="card card-front" aria-label="Business card front">
    <div class="brand-lockup">
      <span class="brand-square"></span>
      <span class="brand-name">Stonegate Builders</span>
    </div>
    <span class="name-marker"></span>
    <h1 class="person-name">Dallin Marsh</h1>
    <p class="person-title">Managing Director</p>
    <span class="divider-line"></span>
    <ul class="contact-list">
      <li class="contact-item">
        <svg class="contact-icon" viewBox="0 0 24 24" aria-hidden="true"><path fill="#52b86a" d="M6.6 10.8a15.1 15.1 0 0 0 6.6 6.6l2.2-2.2a1 1 0 0 1 1-.25 11.4 11.4 0 0 0 3.6.57 1 1 0 0 1 1 1V20a1 1 0 0 1-1 1A17 17 0 0 1 3 4a1 1 0 0 1 1-1h3.5a1 1 0 0 1 1 1c0 1.25.2 2.45.57 3.6a1 1 0 0 1-.25 1z"/></svg>
        <span>0491 555 017</span>
      </li>
      <li class="contact-item">
        <svg class="contact-icon" viewBox="0 0 24 24" aria-hidden="true"><path fill="#52b86a" d="M3 5h18v14H3z"/><path fill="none" stroke="#0f1c20" stroke-width="1.8" d="M3 6l9 7 9-7"/></svg>
        <span>info@stonegatebuilders.com</span>
      </li>
      <li class="contact-item">
        <svg class="contact-icon" viewBox="0 0 24 24" aria-hidden="true"><circle cx="12" cy="12" r="9.5" fill="none" stroke="#52b86a" stroke-width="2"/><path fill="none" stroke="#52b86a" stroke-width="1.6" d="M2.5 12h19M12 2.5c3 3 3 16 0 19M12 2.5c-3 3-3 16 0 19"/></svg>
        <span>www.stonegatebuilders.com</span>
      </li>
    </ul>
    <address class="office-address" style="font-style:normal">
      1480 W Harlan Street<br>
      Maple County 5230
    </address>
    <span class="bottom-band"></span>
  </section>

  <section class="card card-back" aria-label="Business card back">
    <div class="back-pattern-area" role="img" aria-label="Repeating faint brand pattern across the card back"></div>
    <div class="back-brand">
      <span class="brand-square"></span>
      <span class="brand-name">Stonegate Builders</span>
    </div>
  </section>
</main>
</body>
</html>
```